New iOS App design for Boston Startup

We are looking for a new app design for our iPhone app. The current app's design feels outdated and we like to add lots of new functionality and a new navigation as well. A complete overhaul therefore!
We want you to design 5 screens that will have changed the most. The complete wireframes of these 5 pages are attached in the requirements document.
Once the winning design is selected we will award the winner with the designing all other screens (40-50 screens based on the same design). This will be a separate project worth $1000. The winning designer can get more follow up work if both sides are happy about the cooperation.
We will give feedback as soon as the first screen has been uploaded for review. Final decision will be made only after all 5 screens are finished.
We hope you give it your best!
Note: will only communicate through PixelHarbor (no skype),
Updates
Reason: Want to give designers a chance to submit their designs as I understand from some, the deadline is too close.
I have raised the award and introduced a 2nd price as well to make it worth your time. I hope you give it your best shot.
Reason: A few of you have asked for an extension of the deadline as time is running out. I will extend by one day. Tell me if you need more.
Industry/Entity Type
Startup
Requirements
Must have
- At least 1 screen before we can give you feedback.
Nice to have
- multiple options of 1 screen to get to a desirable design

```html
<!DOCTYPE html>
<html lang="en">
<head>
<meta charset="utf-8">
<title>Analytics</title>
<link rel="stylesheet" href="https://fonts.googleapis.com/css2?family=Arimo:wght@400;700&family=Open+Sans:wght@300&family=Source+Sans+3:wght@400&display=swap">
<style>
  :root {
    --status-black: #000000;
    --header-red: #F05052;
    --white: #FFFFFF;
    --ink: #111111;
    --muted: #4a4a4a;
    --strip-bg: rgba(218, 221, 228, 0.85);
    --strip-line: #9aa0a8;
    --up-green: #3DBE4A;
    --down-red: #E53935;
    --bar-track: #DCDCDC;
    --bar-green: #44C04F;
    --bar-blue: #3E9FE0;
    --bar-orange: #FBB127;
    --tab-icon: #5a5a5a;
    --tab-label: #7a7a7a;
    --divider: #e2e2e2;
  }
  * { margin: 0; padding: 0; box-sizing: border-box; }
  html, body { width: 676px; height: 1200px; overflow: hidden; background: var(--white); }
  body { font-family: "Arimo", Helvetica, Arial, sans-serif; position: relative; }

  .status-bar {
    position: absolute; left: 0; top: 0; width: 676px; height: 42px;
    background: var(--status-black); color: var(--white);
    font-size: 23px; font-weight: 700;
  }
  .status-bar .signal { position: absolute; left: 8px; top: 10px; }
  .status-bar .carrier { position: absolute; left: 55px; top: 7px; }
  .status-bar .time { position: absolute; left: 0; right: 0; top: 7px; text-align: center; }
  .status-bar .right { position: absolute; right: 8px; top: 9px; display: flex; gap: 14px; align-items: center; }

  .app-header {
    position: absolute; left: 0; top: 42px; width: 676px; height: 93px;
    background: var(--header-red);
  }
  .app-header .back { position: absolute; left: 25px; top: 27px; }
  .app-header h1 {
    position: absolute; left: 0; right: 0; top: 20px; text-align: center;
    font-family: "Open Sans", Helvetica, sans-serif;
    color: var(--white); font-weight: 300; font-size: 40px; line-height: 54px;
  }

  .hero {
    position: absolute; left: 0; top: 135px; width: 676px; height: 351px;
    background: linear-gradient(180deg, #aab4c2 0%, #8f9db0 45%, #76859a 75%, #6f7a8c 100%);
  }
  .score { position: absolute; top: 0; left: 0; width: 676px; height: 254px; color: var(--ink); }
  .score .label { position: absolute; left: 125px; top: 110px; font-size: 53px; line-height: 60px; }
  .score .value { position: absolute; left: 299px; top: 100px; font-size: 72px; line-height: 80px; }
  .score .arrow { position: absolute; left: 430px; top: 109px; }
  .score .delta { position: absolute; left: 467px; top: 122px; color: var(--white); font-size: 31px; line-height: 36px; }

  .stats-strip {
    position: absolute; left: 0; top: 389px; width: 676px; height: 97px;
    background: var(--strip-bg);
  }
  .stat-num {
    position: absolute; top: 6px; font-size: 35px; line-height: 42px; color: var(--ink);
    display: flex; align-items: center; gap: 1px;
  }
  .stat-name { position: absolute; top: 54px; font-size: 28px; line-height: 32px; color: var(--muted); }
  .stat-period { position: absolute; left: 543px; top: 46px; font-size: 28px; line-height: 32px; color: var(--muted); }
  .strip-divider { position: absolute; top: 0; width: 1px; height: 97px; background: var(--strip-line); }

  .tab-band { position: absolute; left: 0; top: 486px; width: 676px; height: 11px; background: var(--header-red); }
  .tab-band .indicator {
    position: absolute; left: 390px; top: 0; width: 158px; height: 12px;
    background: var(--status-black); box-shadow: inset 0 0 0 2px #000, inset 0 0 0 3px #555;
  }

  .skill { position: absolute; left: 0; width: 676px; height: 49px; }
  .skill .name {
    position: absolute; left: 21px; top: 12px;
    font-family: "Source Sans 3", "Myriad Pro", sans-serif; font-size: 22px; line-height: 28px; color: var(--ink);
  }
  .skill .track {
    position: absolute; left: 278px; top: 0; width: 374px; height: 49px;
    background: var(--bar-track); border-radius: 4px;
    box-shadow: 2px 3px 3px rgba(0,0,0,0.28); overflow: hidden;
  }
  .skill .fill {
    height: 100%; border-radius: 4px 0 0 4px;
    font-family: "Source Sans 3", sans-serif; font-size: 26px; line-height: 49px; color: var(--ink);
    padding-left: 9px;
  }
  .fill.green { background: var(--bar-green); }
  .fill.blue { background: var(--bar-blue); }
  .fill.orange { background: var(--bar-orange); }

  .bottom-divider { position: absolute; left: 0; top: 1060px; width: 676px; height: 3px; background: var(--divider); }

  .tab { position: absolute; top: 1090px; width: 120px; margin-left: -60px; height: 100px; }
  .tab svg { position: absolute; left: 50%; bottom: 40px; transform: translateX(-50%); }
  .tab .label {
    position: absolute; left: 0; right: 0; top: 70px; text-align: center;
    font-size: 20px; line-height: 24px; color: var(--tab-label);
  }
</style>
</head>
<body>

<div class="status-bar">
  <svg class="signal" width="40" height="22" viewBox="0 0 40 22" aria-hidden="true">
    <rect x="0" y="16" width="5" height="6" fill="#fff"/>
    <rect x="8" y="12" width="5" height="10" fill="#fff"/>
    <rect x="16" y="8" width="5" height="14" fill="#fff"/>
    <rect x="24" y="4" width="5" height="18" fill="#fff"/>
    <rect x="32" y="0" width="5" height="22" fill="#fff"/>
  </svg>
  <span class="carrier">VESTA&nbsp;&nbsp;3G</span>
  <div class="time">9:51 PM</div>
  <div class="right">
    <svg width="22" height="22" viewBox="0 0 22 22" aria-hidden="true">
      <circle cx="11" cy="11" r="10" fill="#fff"/>
      <path d="M11 5 V11 H15" stroke="#000" stroke-width="2" fill="none"/>
    </svg>
    <svg width="46" height="24" viewBox="0 0 46 24" aria-hidden="true">
      <rect x="1" y="1" width="40" height="22" rx="3" fill="none" stroke="#fff" stroke-width="2"/>
      <rect x="4" y="4" width="34" height="16" fill="#fff"/>
      <rect x="42" y="8" width="3" height="8" fill="#fff"/>
    </svg>
  </div>
</div>

<header class="app-header">
  <svg class="back" width="42" height="42" viewBox="0 0 42 42" aria-label="Back">
    <circle cx="21" cy="21" r="20" fill="#fff"/>
    <path d="M10 21 L20 11 V17 H31 V25 H20 V31 Z" fill="var(--header-red)"/>
  </svg>
  <h1>Analytics</h1>
</header>

<section class="hero" role="img" aria-label="Background photo of a calm misty waterscape">
  <div class="score">
    <span class="label">Score</span>
    <span class="value">650</span>
    <svg class="arrow" width="34" height="60" viewBox="0 0 34 60" aria-hidden="true">
      <path d="M11 2 H23 V36 H32 L17 58 L2 36 H11 Z" fill="var(--down-red)" stroke="#8a1c1c" stroke-width="1"/>
    </svg>
    <span class="delta">-18</span>
  </div>
</section>

<div class="stats-strip">
  <div class="stat-num" style="left:31px">34%<svg width="20" height="32" viewBox="0 0 20 32" aria-hidden="true"><path d="M10 1 L19 13 H13 V31 H7 V13 H1 Z" fill="var(--up-green)" stroke="#1f7a2a" stroke-width="1"/></svg>+4</div>
  <div class="stat-name" style="left:35px">Completion</div>
  <div class="strip-divider" style="left:222px"></div>
  <div class="stat-num" style="left:251px">20<svg width="20" height="32" viewBox="0 0 20 32" aria-hidden="true"><path d="M10 1 L19 13 H13 V31 H7 V13 H1 Z" fill="var(--up-green)" stroke="#1f7a2a" stroke-width="1"/></svg>+3</div>
  <div class="stat-name" style="left:246px">Sessions</div>
  <div class="stat-num" style="left:395px">18<svg width="20" height="32" viewBox="0 0 20 32" aria-hidden="true"><path d="M10 1 L19 13 H13 V31 H7 V13 H1 Z" fill="var(--up-green)" stroke="#1f7a2a" stroke-width="1"/></svg>+10</div>
  <div class="stat-name" style="left:398px">Min.</div>
  <div class="strip-divider" style="left:527px"></div>
  <div class="stat-period">This week</div>
</div>

<div class="tab-band"><div class="indicator"></div></div>

<section class="skills">
  <div class="skill" style="top:551px">
    <span class="name">Sentence Correction</span>
    <div class="track"><div class="fill green" style="width:227px">710</div></div>
  </div>
  <div class="skill" style="top:637px">
    <span class="name">Critical Reasoning</span>
    <div class="track"><div class="fill blue" style="width:79px">225</div></div>
  </div>
  <div class="skill" style="top:721px">
    <span class="name">Reading Comprehension</span>
    <div class="track"><div class="fill orange" style="width:174px">465</div></div>
  </div>
  <div class="skill" style="top:808px">
    <span class="name">Data Sufficiency</span>
    <div class="track"><div class="fill green" style="width:227px">710</div></div>
  </div>
  <div class="skill" style="top:892px">
    <span class="name">Problem Solving</span>
    <div class="track"><div class="fill blue" style="width:79px">225</div></div>
  </div>
  <div class="skill" style="top:979px">
    <span class="name">Pace</span>
    <div class="track"><div class="fill orange" style="width:174px">465</div></div>
  </div>
</section>

<div class="bottom-divider"></div>

<nav class="tab-bar">
  <div class="tab" style="left:79px">
    <svg width="66" height="48" viewBox="0 0 66 48" aria-hidden="true">
      <rect x="4" y="2" width="50" height="7" fill="var(--tab-icon)"/>
      <rect x="10" y="14" width="54" height="8" fill="var(--tab-icon)"/>
      <rect x="2" y="26" width="52" height="8" fill="var(--tab-icon)"/>
      <rect x="8" y="38" width="52" height="9" fill="var(--tab-icon)"/>
    </svg>
    <span class="label">Theory</span>
  </div>
  <div class="tab" style="left:208px">
    <svg width="50" height="56" viewBox="0 0 50 56" aria-hidden="true">
      <rect x="3" y="6" width="40" height="48" rx="3" fill="none" stroke="var(--tab-icon)" stroke-width="3"/>
      <rect x="15" y="1" width="16" height="9" rx="2" fill="var(--tab-icon)"/>
      <rect x="20" y="20" width="26" height="32" fill="#fff" stroke="var(--tab-icon)" stroke-width="2"/>
      <path d="M24 27 H42 M24 33 H42 M24 39 H42 M24 45 H42" stroke="var(--tab-icon)" stroke-width="2"/>
    </svg>
    <span class="label">Practice</span>
  </div>
  <div class="tab" style="left:340px">
    <svg width="56" height="52" viewBox="0 0 56 54" aria-hidden="true">
      <path d="M28 2 L54 26 H47 V52 H34 V36 H22 V52 H9 V26 H2 Z" fill="var(--tab-icon)"/>
      <rect x="40" y="6" width="7" height="14" fill="var(--tab-icon)"/>
    </svg>
    <span class="label">Home</span>
  </div>
  <div class="tab" style="left:475px">
    <svg width="58" height="40" viewBox="0 8 58 42" aria-hidden="true">
      <path d="M14 12 H44 C52 12 56 24 56 36 C56 46 50 48 44 40 L40 34 H18 L14 40 C8 48 2 46 2 36 C2 24 6 12 14 12 Z" fill="var(--tab-icon)"/>
      <path d="M12 24 H22 M17 19 V29" stroke="#fff" stroke-width="3"/>
      <circle cx="40" cy="21" r="2.5" fill="#fff"/>
      <circle cx="46" cy="26" r="2.5" fill="#fff"/>
    </svg>
    <span class="label">Games</span>
  </div>
  <div class="tab" style="left:607px">
    <svg width="52" height="56" viewBox="0 0 52 56" aria-hidden="true">
      <rect x="3" y="5" width="38" height="48" fill="none" stroke="var(--tab-icon)" stroke-width="3"/>
      <path d="M10 18 H34 M10 25 H34 M10 32 H34 M10 39 H34 M10 46 H28" stroke="var(--tab-icon)" stroke-width="2"/>
      <path d="M30 10 L37 17 L50 2" stroke="var(--tab-icon)" stroke-width="4" fill="none"/>
    </svg>
    <span class="label">Test</span>
  </div>
</nav>

</body>
</html>
```